Copper Lantern

Need a business card for our restaurant. Restaurant and Bar in the mountains of North Idaho. Rustic looking card

rustic design, wood and metal looking, primarily neutral colors

• Name, address, phone number, website, email address

```html
<!DOCTYPE html>
<html lang="en">
<head>
<meta charset="utf-8">
<title>Copper Lantern – Business Card</title>
<link href="https://fonts.googleapis.com/css2?family=Lato:wght@400;700&family=Permanent+Marker&display=swap" rel="stylesheet">
<style>
  :root {
    --page: #262626;
    --card-black: #111111;
    --card-black-2: #232323;
    --card-white: #ffffff;
    --stone: #d4d4d4;
    --stone-light: #e4e4e4;
    --metal-hi: #e6e6e6;
    --metal-lo: #6e6e6e;
    --ink: #f0f0f0;
    --ink-soft: #d6d6d6;
    --mark: #151515;
    --scratch: rgba(255,255,255,.045);
    --scratch-2: rgba(255,255,255,.03);
  }
  html, body {
    margin: 0;
    width: 1200px;
    height: 875px;
    overflow: hidden;
    background: var(--page);
    font-family: "Lato", sans-serif;
  }
  .canvas { position: relative; width: 1200px; height: 875px; }

  .card {
    position: absolute;
    width: 700px;
    height: 400px;
    border-radius: 22px;
    overflow: hidden;
    box-shadow: 0 20px 44px rgba(0,0,0,.55);
  }

  /* Rustic worn-metal surface shared by dark areas */
  .rustic {
    background:
      repeating-linear-gradient(23deg, transparent 0 9px, var(--scratch) 9px 10px, transparent 10px 23px),
      repeating-linear-gradient(-38deg, transparent 0 14px, var(--scratch-2) 14px 15px, transparent 15px 31px),
      repeating-linear-gradient(71deg, transparent 0 19px, var(--scratch-2) 19px 20px, transparent 20px 41px),
      radial-gradient(circle at 30% 35%, rgba(255,255,255,.07), transparent 45%),
      radial-gradient(circle at 75% 70%, rgba(255,255,255,.05), transparent 40%),
      linear-gradient(135deg, var(--card-black-2), var(--card-black));
  }

  /* Back side */
  .card-back { left: 60px; top: 30px; }
  .card-back .pattern {
    position: absolute; left: 24px; top: 24px; width: 560px; height: 352px;
    border-radius: 10px;
    background:
      linear-gradient(100deg, rgba(230,230,230,.38) 0%, rgba(150,150,150,.2) 30%, rgba(90,90,90,.1) 60%, rgba(40,40,40,0) 90%);
    -webkit-mask: repeating-linear-gradient(90deg, #000 0 34px, transparent 34px 60px),
                  repeating-linear-gradient(0deg, #000 0 30px, transparent 30px 52px);
    -webkit-mask-composite: source-in;
    mask: repeating-linear-gradient(90deg, #000 0 34px, transparent 34px 60px),
          repeating-linear-gradient(0deg, #000 0 30px, transparent 30px 52px);
    mask-composite: intersect;
  }
  .card-back .back-name {
    position: absolute; right: 46px; top: 182px;
    display: flex; align-items: center; gap: 10px;
    color: var(--ink); font-size: 18px; font-weight: 700; letter-spacing: .04em;
  }
  .dot { width: 12px; height: 12px; border-radius: 50%; background: var(--ink); flex: none; }

  /* Front side */
  .card-front { left: 440px; top: 445px; background: var(--card-white); }
  .front-dark { position: absolute; left: 0; top: 0; bottom: 0; width: 470px; }
  .front-art { position: absolute; left: 300px; top: 0; width: 400px; height: 400px; }
  .front-logo {
    position: absolute; right: 34px; top: 56px;
    display: flex; align-items: center; gap: 10px;
    color: var(--mark); font-size: 20px; font-weight: 700; letter-spacing: .03em;
  }
  .front-logo .dot { background: var(--mark); }

  .contact { position: absolute; left: 40px; top: 196px; color: var(--ink); }
  .contact .person {
    margin: 0; font-family: "Permanent Marker", cursive;
    font-size: 32px; font-weight: 400; letter-spacing: .05em;
    text-transform: uppercase; color: var(--ink); line-height: 1.1;
  }
  .contact .role { margin: 4px 0 14px; font-size: 17px; color: var(--ink-soft); }
  .contact ul { list-style: none; margin: 0; padding: 0; }
  .contact li {
    display: flex; align-items: center; gap: 10px;
    font-size: 15px; line-height: 26px; color: var(--ink-soft);
  }
  .contact svg { width: 13px; height: 13px; fill: var(--ink-soft); flex: none; }
</style>
</head>
<body>
<div class="canvas">

  <section class="card card-back rustic" aria-label="Card back">
    <div class="pattern" role="img" aria-label="Repeating metallic brand pattern across dark textured surface"></div>
    <div class="back-name"><span class="dot"></span>Copper Lantern</div>
  </section>

  <section class="card card-front" aria-label="Card front">
    <div class="front-dark rustic"></div>
    <svg class="front-art" viewBox="0 0 400 400" role="img" aria-label="Large light grey animal illustration spanning the card">
      <defs>
        <linearGradient id="stoneFill" x1="0" y1="0" x2="1" y2="1">
          <stop offset="0" stop-color="var(--stone-light)"/>
          <stop offset="1" stop-color="var(--stone)"/>
        </linearGradient>
      </defs>
      <path d="M170 0 H400 V400 H90 C140 340 90 280 120 230 C70 200 40 120 80 70 C110 40 150 30 170 0 Z" fill="url(#stoneFill)"/>
      <path d="M250 0 H400 V400 H200 C250 330 215 260 250 190 C280 130 240 60 250 0 Z" fill="var(--card-white)"/>
    </svg>
    <div class="front-logo"><span class="dot"></span>Copper Lantern</div>

    <div class="contact">
      <h1 class="person">Daniel Reeves</h1>
      <p class="role">Founder &amp; CEO</p>
      <ul>
        <li><svg viewBox="0 0 16 16"><path d="M3 1l3 3-2 2c1 2 3 4 5 5l2-2 3 3-2 3C6 15 1 10 1 3z"/></svg>(208) 555-0147</li>
        <li><svg viewBox="0 0 16 16"><path d="M1 3h14v10H1zM1 3l7 6 7-6" stroke="var(--card-black)" stroke-width="1"/></svg>info@copperlanternidaho.com</li>
        <li><svg viewBox="0 0 16 16"><circle cx="8" cy="8" r="7"/></svg>copperlanternidaho.com</li>
        <li><svg viewBox="0 0 16 16"><path d="M8 1a5 5 0 0 1 5 5c0 4-5 9-5 9S3 10 3 6a5 5 0 0 1 5-5z"/></svg>214 Pine Ridge Rd, Cedar Falls, ID 83800</li>
      </ul>
    </div>
  </section>

</div>
</body>
</html>
```